Business Card Design

Hi I need a business card designed, we already have the business name logo artwork and would like some concept ideas for the Bus Card layout.
On the back of the card i want to include the products and services that we offer.
We are a Plastics Sheeting manufacture based in Perth Australia.

                                       

We need a BC design for a company called Tarvo Plastics based in Perth Australia.

We supply from DIY to Trade & Industrial  Engineering Markets.

We specialise in:

·         Cut to size panels  (all shapes and sizes)

·         Plastics fabrication & Welding

·         Custom Designs

·         Plastic Repairs

·         PVC Pipe Slotting & PVC Pipe Threading

·         Supplier of all types of engineering plastics and profiles.

Including:           Acrylic / Clarvene

                               Polycarbonate / Dorvil

                               Prismatic Light Diffuser

                               Vantrib

                               HDPE / UHMWPE

                               PVC / PVC Foam

                               Nylon

                               HIPS

```html
<!DOCTYPE html>
<html lang="en">
<head>
<meta charset="utf-8">
<title>Tarvo Plastics – Business Card</title>
<link rel="stylesheet" href="https://fonts.googleapis.com/css2?family=PT+Sans:ital,wght@0,400;0,700;1,700&display=swap">
<style>
  :root {
    --navy: #1b2a5c;
    --bullet-blue: #2a8fd6;
    --ink-grey: #4a4a4a;
    --paper: #ffffff;
    --backdrop: #e4e5ea;
    --faint: #eceef3;
    --rule: #8d96b8;
  }
  * { box-sizing: border-box; margin: 0; padding: 0; }
  html, body { width: 1200px; height: 987px; overflow: hidden; }
  body {
    background: var(--backdrop);
    font-family: "PT Sans", Arial, sans-serif;
    position: relative;
  }
  .card {
    position: absolute;
    width: 760px;
    height: 437px;
    background: var(--paper);
    border-radius: 26px;
    overflow: hidden;
    box-shadow: 0 6px 18px rgba(0,0,0,0.12);
  }
  /* ---------- Back ---------- */
  .card-back { left: 390px; top: 40px; }
  .card-back .watermark {
    position: absolute;
    left: 0; right: 0; top: 150px;
    text-align: center;
    font-size: 120px;
    font-weight: 700;
    color: var(--faint);
    white-space: nowrap;
  }
  .card-back .content {
    position: relative;
    padding: 34px 40px 0;
    text-align: center;
  }
  .offer-heading {
    color: var(--navy);
    font-style: italic;
    font-weight: 700;
    font-size: 21px;
    line-height: 1.2;
  }
  .section-title {
    color: var(--navy);
    font-weight: 700;
    font-size: 27px;
    margin-top: 16px;
    line-height: 1.1;
  }
  .item-line {
    color: var(--ink-grey);
    font-size: 19px;
    line-height: 1.32;
  }
  .item-line .dot {
    display: inline-block;
    width: 7px; height: 7px;
    border-radius: 50%;
    background: var(--bullet-blue);
    margin: 0 5px 3px 10px;
  }
  .item-line .dot:first-child { margin-left: 0; }
  /* ---------- Front ---------- */
  .card-front { left: 60px; top: 510px; }
  .brand-name {
    position: absolute;
    left: 0; right: 0; top: 28px;
    text-align: center;
    color: var(--navy);
    font-weight: 700;
    font-size: 78px;
    line-height: 1;
  }
  .contact-band {
    position: absolute;
    left: 0; right: 0;
    top: 140px; height: 232px;
    background: var(--navy);
    color: var(--paper);
  }
  .identity {
    position: absolute;
    right: 410px; top: 22px;
    text-align: right;
    font-size: 20px;
    line-height: 1.3;
  }
  .identity .person { font-weight: 700; font-size: 25px; }
  .identity .role { margin-bottom: 6px; }
  .divider {
    position: absolute;
    left: 366px; top: 70px;
    width: 1px; height: 120px;
    background: var(--rule);
  }
  .channels {
    position: absolute;
    left: 392px; top: 78px;
    list-style: none;
    font-size: 21px;
    line-height: 1.5;
  }
  .channels li { display: flex; align-items: center; gap: 10px; }
  .channels svg { width: 18px; height: 18px; fill: var(--paper); flex: none; }
  .legal-line {
    position: absolute;
    left: 0; right: 0; bottom: 22px;
    text-align: center;
    color: var(--ink-grey);
    font-size: 19px;
  }
</style>
</head>
<body>

<section class="card card-back" aria-label="Card back">
  <div class="watermark" aria-hidden="true">Tarvo Plastics</div>
  <div class="content">
    <p class="offer-heading">The Products And Services That We Offer<br>Are Supplied From DIY To Trade &amp; Industrial Engineering Markets</p>

    <h2 class="section-title">We specialise in:</h2>
    <p class="item-line"><span class="dot"></span>Cut to size panels (all shapes and sizes)</p>
    <p class="item-line"><span class="dot"></span>Plastics fabrication &amp; Welding <span class="dot"></span>Custom Designs</p>
    <p class="item-line"><span class="dot"></span>Plastic Repairs <span class="dot"></span>PVC Pipe Slotting &amp; PVC Pipe Threading</p>
    <p class="item-line"><span class="dot"></span>Supplier of all types of engineering plastics and profiles</p>

    <h2 class="section-title">Including:</h2>
    <p class="item-line"><span class="dot"></span>Acrylic / Clarvene <span class="dot"></span>Polycarbonate / Dorvil</p>
    <p class="item-line"><span class="dot"></span>Prismatic Light Diffuser <span class="dot"></span>Vantrib <span class="dot"></span>HDPE / UHMWPE</p>
    <p class="item-line"><span class="dot"></span>PVC / PVC Foam <span class="dot"></span>Nylon <span class="dot"></span>HIPS</p>
  </div>
</section>

<section class="card card-front" aria-label="Card front">
  <h1 class="brand-name">Tarvo Plastics</h1>

  <div class="contact-band">
    <div class="identity">
      <p class="person">Your Name</p>
      <p class="role">Title</p>
      <p>Unit 4/18 Harlow Crescent</p>
      <p>Kestrel Vale WA 6155</p>
      <p>PO Box 2240</p>
      <p>Kestrel Vale DC WA 6970</p>
    </div>

    <div class="divider"></div>

    <ul class="channels">
      <li>
        <svg viewBox="0 0 24 24" aria-hidden="true"><path d="M6.6 10.8a15 15 0 0 0 6.6 6.6l2.2-2.2a1 1 0 0 1 1-.25 11.4 11.4 0 0 0 3.6.57 1 1 0 0 1 1 1V20a1 1 0 0 1-1 1A17 17 0 0 1 3 4a1 1 0 0 1 1-1h3.5a1 1 0 0 1 1 1c0 1.25.2 2.45.57 3.6a1 1 0 0 1-.25 1z"/></svg>
        <span>08 9300 4417</span>
      </li>
      <li>
        <svg viewBox="0 0 24 24" aria-hidden="true"><path d="M8 1h8a2 2 0 0 1 2 2v18a2 2 0 0 1-2 2H8a2 2 0 0 1-2-2V3a2 2 0 0 1 2-2zm0 3v13h8V4zm4 15a1.2 1.2 0 1 0 0 2.4 1.2 1.2 0 0 0 0-2.4z"/></svg>
        <span>123-456-7890</span>
      </li>
      <li>
        <svg viewBox="0 0 24 24" aria-hidden="true"><path d="M7 2h9l3 3v5h1a2 2 0 0 1 2 2v8a2 2 0 0 1-2 2H4a2 2 0 0 1-2-2v-8a2 2 0 0 1 2-2h3zm2 2v6h8V6h-3V4zm-3 10v2h3v-2zm5 0v2h3v-2zm5 0v2h3v-2z"/></svg>
        <span>08 9300 4418</span>
      </li>
      <li>
        <svg viewBox="0 0 24 24" aria-hidden="true"><path d="M2 5h20v14H2zm2 2v.4l8 5 8-5V7zm0 2.7V17h16V9.7l-8 5z"/></svg>
        <span>sales@tarvoplastics.com.au</span>
      </li>
    </ul>
  </div>

  <p class="legal-line">Nerrin Holdings Pty Ltd T/A Tarvo Plastics ABN: TBA</p>
</section>

</body>
</html>
```